The Plate Compass

Cutting Through the Noise to What Actually Works.

Nutrition book

Target Market(s)

People looking to be or get healthy and eat right.

```html
<!DOCTYPE html>
<html lang="en">
<head>
<meta charset="UTF-8">
<title>The Plate Compass – Book Cover</title>
<link href="https://fonts.googleapis.com/css2?family=Playfair+Display:wght@700;800&family=Poppins:wght@500;700&display=swap" rel="stylesheet">
<style>
  :root {
    --mint: #e3f8e2;
    --photo-tone: #c9e6c2;
    --forest: #1f3a17;
    --ink: #0d0d0d;
    --icon-stroke: #1a1a1a;
  }
  * { margin: 0; padding: 0; box-sizing: border-box; }
  html, body {
    width: 858px;
    height: 1200px;
    overflow: hidden;
    background: var(--mint);
  }
  .cover {
    position: relative;
    width: 858px;
    height: 1200px;
    background: var(--mint);
    overflow: hidden;
    font-family: "Poppins", sans-serif;
  }
  .title-the {
    position: absolute;
    top: 70px;
    left: 0;
    width: 100%;
    display: flex;
    align-items: center;
    justify-content: center;
    gap: 22px;
  }
  .title-rule {
    width: 228px;
    height: 3px;
    background: linear-gradient(90deg, transparent, var(--forest) 30%, var(--forest));
  }
  .title-rule.right {
    background: linear-gradient(90deg, var(--forest), var(--forest) 70%, transparent);
  }
  .title-the-word {
    font-family: "Playfair Display", serif;
    font-weight: 700;
    font-size: 60px;
    line-height: 1;
    color: var(--ink);
  }
  .title-main {
    position: absolute;
    left: 0;
    width: 100%;
    text-align: center;
    font-family: "Playfair Display", serif;
    font-weight: 800;
    font-size: 104px;
    line-height: 1;
    letter-spacing: -1px;
  }
  .title-plate { top: 138px; color: var(--forest); }
  .title-compass { top: 250px; color: var(--ink); }

  .hierarchy { list-style: none; }
  .hierarchy-item {
    position: absolute;
    display: flex;
    align-items: center;
    gap: 11px;
    height: 34px;
    font-weight: 500;
    font-size: 18px;
    line-height: 1;
    letter-spacing: 0.2px;
    color: var(--ink);
    white-space: nowrap;
  }
  .hierarchy-item svg {
    width: 34px;
    height: 34px;
    flex: none;
    fill: none;
    stroke: var(--icon-stroke);
    stroke-width: 1.4;
    stroke-linecap: round;
    stroke-linejoin: round;
  }
  .item-noise       { left: 616px; top: 393px; }
  .item-supplements { left: 443px; top: 453px; }
  .item-timing      { left: 335px; top: 521px; }
  .item-quality     { left: 200px; top: 586px; }
  .item-protein     { left: 159px; top: 659px; }
  .item-calories    { left: 94px;  top: 730px; }

  .salad-photo {
    position: absolute;
    left: 250px;
    top: 480px;
    width: 608px;
    height: 520px;
    background: radial-gradient(ellipse 55% 50% at 55% 55%, var(--photo-tone) 0%, rgba(201,230,194,0.6) 55%, rgba(227,248,226,0) 100%);
  }

  .tagline {
    position: absolute;
    top: 1058px;
    left: 0;
    width: 100%;
    text-align: center;
    font-weight: 700;
    font-size: 29px;
    line-height: 39px;
    letter-spacing: 0.3px;
    color: var(--forest);
    text-transform: uppercase;
  }
</style>
</head>
<body>
<main class="cover">
  <header>
    <div class="title-the">
      <span class="title-rule"></span>
      <span class="title-the-word">THE</span>
      <span class="title-rule right"></span>
    </div>
    <h1>
      <span class="title-main title-plate">PLATE</span>
      <span class="title-main title-compass">COMPASS</span>
    </h1>
  </header>

  <div class="salad-photo" role="img" aria-label="Photo of a dark bowl of fresh salad with lettuce, tomatoes, cucumber and red onion flying up out of it"></div>

  <ul class="hierarchy">
    <li class="hierarchy-item item-noise">
      <svg viewBox="0 0 32 32" aria-hidden="true">
        <path d="M3 13v6M7 10v12M11 6v20M15 11v10M19 4v24M23 9v14M27 12v8M30 14v4"/>
      </svg>
      NOISE
    </li>
    <li class="hierarchy-item item-supplements">
      <svg viewBox="0 0 32 32" aria-hidden="true">
        <rect x="12" y="2" width="14" height="4" rx="1"/>
        <path d="M13 6v3h12V6M11 11q0-2 2-2h12q2 0 2 2v18H11z"/>
        <circle cx="19" cy="19" r="4"/>
        <path d="M17 20q2-4 4-2"/>
        <rect x="2" y="24" width="9" height="5" rx="2.5"/>
        <circle cx="7" cy="20" r="3"/>
      </svg>
      SUPPLEMENTS
    </li>
    <li class="hierarchy-item item-timing">
      <svg viewBox="0 0 32 32" aria-hidden="true">
        <circle cx="16" cy="16" r="14.5"/>
        <circle cx="16" cy="16" r="11.5"/>
        <path d="M16 9v7l5 3"/>
      </svg>
      MEAL TIMING
    </li>
    <li class="hierarchy-item item-quality">
      <svg viewBox="0 0 32 32" aria-hidden="true">
        <path d="M16 2l3 3 4-1 1 4 4 1-1 4 3 3-3 3 1 4-4 1-1 4-4-1-3 3-3-3-4 1-1-4-4-1 1-4-3-3 3-3-1-4 4-1 1-4 4 1z"/>
        <circle cx="16" cy="16" r="8"/>
        <path d="M12.5 16l2.5 2.5 4.5-5"/>
      </svg>
      FOOD QUALITY
    </li>
    <li class="hierarchy-item item-protein">
      <svg viewBox="0 0 32 32" aria-hidden="true">
        <circle cx="16" cy="16" r="14.5"/>
        <path d="M8 10q4-3 6 1t6 1M12 16q4-3 6 1t6 1M10 22q4-3 6 1"/>
      </svg>
      PROTEIN
    </li>
    <li class="hierarchy-item item-calories">
      <svg viewBox="0 0 32 32" aria-hidden="true">
        <path d="M14 29C7 29 4 24 5 18c1-4 4-6 5-10 2 3 2 5 2 7 2-4 4-9 3-13 5 4 9 10 9 16"/>
        <rect x="12" y="22" width="18" height="8" rx="1.5"/>
        <text x="21" y="28.5" font-size="6" font-family="Poppins, sans-serif" text-anchor="middle" fill="#1a1a1a" stroke="none">kcal</text>
      </svg>
      CALORIES
    </li>
  </ul>

  <p class="tagline">Cutting through the noise to what<br>actually works.</p>
</main>
</body>
</html>
```